Business card for denture clinic Veltrimora

We need a new business card with our new logo. We are a denture clinic in New Zealand with our target market being 45+ years old. We would need a space on the back to write our patients next appointment on. We would space for only one appointment rather than a list. We will attach a photo showing an example of this. But of course, we would like to see your twist on this. We want it to be bold and easy to read and a good mixture of professional but modern. We have attached our logo to be used on the card.

Target Market(s)

People aged 45+ needing dentures

Industry/Entity Type

Dental

Contact Information for Business Card

We want our logo on the front and the space to write an appointment on the back. I've attached an example our our old business card showing this. We need to have the technicians details on the front.

Font styles to use
Sans Serif

Colors
0255a3
919191
fbfbfb

Requirements
Must have
• The following details:
• Liam Dorsett BDT, PGDipCDentTech Calverin
• Dental Prosthetist
• Phone numbers: 0800 47 3125
• 09 572 1394
• Email: liam@veltrimora.co.nz
• www.veltrimora.co.nz
• Address: 14 Marlow Crest Road
• Halbrook West
• Auckland 0793
Nice to have
• We would like our business cards to have more than just two colours as we want them to be more vibrant. We have uploaded an example of a business card we liked that showed this.

```html
<!DOCTYPE html>
<html lang="en">
<head>
<meta charset="utf-8">
<title>Veltrimora Business Card</title>
<link href="https://fonts.googleapis.com/css2?family=Lato:ital,wght@0,400;0,700;0,900;1,400&display=swap" rel="stylesheet">
<style>
  :root {
    --brand-blue: #0255a3;
    --brand-grey: #919191;
    --paper: #fbfbfb;
    --paper-tint: #f3f3f3;
    --backdrop: #ececec;
    --white: #ffffff;
  }
  * { margin: 0; padding: 0; box-sizing: border-box; }
  html, body {
    width: 1200px; height: 586px; overflow: hidden;
    background: var(--backdrop);
    font-family: 'Lato', sans-serif;
  }
  .canvas { position: relative; width: 1200px; height: 586px; }
  .card {
    position: absolute; top: 129px; width: 501px; height: 300px;
    background: repeating-linear-gradient(135deg, var(--paper) 0 3px, var(--paper-tint) 3px 4px);
    overflow: hidden;
  }
  .card--back { left: 61px; }
  .card--front { left: 619px; }

  .stripe { position: absolute; left: 0; width: 100%; height: 3px; background: var(--brand-blue); }
  .band { position: absolute; left: 0; bottom: 0; width: 100%; background: var(--brand-blue); }

  /* back: appointment */
  .appointment-title {
    position: absolute; top: 40px; left: 0; width: 100%; text-align: center;
    color: var(--brand-blue); font-weight: 700; font-size: 13px; letter-spacing: 4.4px;
  }
  .appointment-title span { border-bottom: 1px solid var(--brand-blue); padding: 0 2px 3px 4px; }
  .field-label { position: absolute; top: 110px; color: var(--brand-blue); font-size: 13px; }
  .field-box {
    position: absolute; top: 133px; width: 189px; height: 40px;
    border: 3px solid var(--brand-blue); border-radius: 7px;
  }
  .back-stripe-1 { top: 210px; }
  .back-stripe-2 { top: 216px; }
  .card--back .band { top: 222px; }
  .wordmark {
    position: absolute; left: 0; width: 100%; text-align: center;
    font-weight: 700; text-transform: uppercase; letter-spacing: 3px;
  }
  .card--back .wordmark { top: 236px; font-size: 28px; color: var(--white); }
  .tagline {
    position: absolute; left: 0; width: 100%; text-align: center;
    font-size: 11.5px; letter-spacing: 3px; text-transform: uppercase;
  }
  .card--back .tagline { top: 268px; color: var(--white); font-weight: 700; }

  /* front: identity */
  .mark-square {
    position: absolute; left: 226px; top: 33px; width: 49px; height: 49px;
    background: var(--brand-blue); border-radius: 2px;
  }
  .card--front .wordmark { top: 84px; font-size: 27px; color: var(--brand-blue); }
  .card--front .tagline { top: 115px; color: var(--brand-grey); }
  .front-stripe-1 { top: 161px; }
  .front-stripe-2 { top: 167px; }
  .card--front .band { top: 174px; }

  .technician { position: absolute; right: 282px; text-align: right; color: var(--white); white-space: nowrap; }
  .technician-name { top: 190px; font-weight: 900; font-size: 15px; }
  .technician-credential { top: 211px; font-style: italic; font-size: 11px; }
  .technician-role { top: 232px; font-weight: 700; font-size: 11px; }
  .technician-address { top: 254px; font-size: 10px; line-height: 14px; }
  .divider {
    position: absolute; left: 232px; top: 186px; width: 1px; height: 104px;
    background: linear-gradient(to bottom, transparent, rgba(255,255,255,.7), transparent);
  }
  .contact { position: absolute; left: 250px; display: flex; align-items: center; color: var(--white); font-size: 12px; white-space: nowrap; }
  .contact svg { width: 16px; height: 16px; margin-right: 8px; flex: none; }
  .contact-1 { top: 189px; }
  .contact-2 { top: 212px; }
  .contact-3 { top: 235px; }
  .contact-4 { top: 258px; }
</style>
</head>
<body>
<div class="canvas">

  <section class="card card--back">
    <h2 class="appointment-title"><span>Your Next Appointment</span></h2>
    <div class="field-label" style="left:39px">Date:</div>
    <div class="field-box" style="left:41px"></div>
    <div class="field-label" style="left:272px">Time:</div>
    <div class="field-box" style="left:274px"></div>
    <div class="stripe back-stripe-1"></div>
    <div class="stripe back-stripe-2"></div>
    <div class="band"></div>
    <div class="wordmark">Veltrimora</div>
    <div class="tagline">The Denture Experts</div>
  </section>

  <section class="card card--front">
    <div class="mark-square"></div>
    <div class="wordmark">Veltrimora</div>
    <div class="tagline">The Denture Experts</div>
    <div class="stripe front-stripe-1"></div>
    <div class="stripe front-stripe-2"></div>
    <div class="band"></div>

    <div class="technician technician-name">Liam Dorsett BDT</div>
    <div class="technician technician-credential">PGDipCDentTech Calverin</div>
    <div class="technician technician-role">Dental Prosthetist</div>
    <address class="technician technician-address" style="font-style:normal">14 Marlow Crest Road<br>Halbrook West, Auckland 0793</address>
    <div class="divider"></div>

    <div class="contact contact-1">
      <svg viewBox="0 0 20 20"><circle cx="10" cy="10" r="10" fill="#fff"/><path d="M5 9c0-2 2-3 5-3s5 1 5 3l-2 1-1-1.5H8L7 10z M7 10.5h6l1 3.5H6z" fill="#0255a3"/></svg>
      <span>0800 47 3125</span>
    </div>
    <div class="contact contact-2">
      <svg viewBox="0 0 20 20"><circle cx="10" cy="10" r="10" fill="#fff"/><path d="M5 9c0-2 2-3 5-3s5 1 5 3l-2 1-1-1.5H8L7 10z M7 10.5h6l1 3.5H6z" fill="#0255a3"/></svg>
      <span>09 572 1394</span>
    </div>
    <div class="contact contact-3">
      <svg viewBox="0 0 20 20"><circle cx="10" cy="10" r="10" fill="#fff"/><rect x="5" y="6.5" width="10" height="7" fill="#0255a3"/><path d="M5.5 7l4.5 3.5L14.5 7" stroke="#fff" stroke-width="1" fill="none"/></svg>
      <span>liam@veltrimora.co.nz</span>
    </div>
    <div class="contact contact-4">
      <svg viewBox="0 0 20 20"><circle cx="10" cy="10" r="10" fill="#fff"/><circle cx="10" cy="10" r="5" fill="none" stroke="#0255a3" stroke-width="1.3"/><path d="M5 10h10M10 5c-2.5 3-2.5 7 0 10M10 5c2.5 3 2.5 7 0 10" fill="none" stroke="#0255a3" stroke-width="1"/></svg>
      <span>www.veltrimora.co.nz</span>
    </div>
  </section>

</div>
</body>
</html>
```